New Wordpress Design Project - Australian native plant nursery

I'm Seeking a wordpress website with landing page with contact details and social links, that page will link to another 4 pages. I'm happy to just add in the information once the template is set up (draft text provided on word doc).
Needing pages of information pages for:
- Nursery, what we carry and that we provide garden design services, pictures of plants and gardens
- Native flowers & what we provide, flower arrangements for weddings, special occasions, pictures
- Giftwear short blurb that we carry local artisan giftwear, pictures
- about us with history of the nursery & pictures
* Also wanting a link for e-gift cards. The link will go to an external page (square) so I don’t need to set up the website for purchases.
Social media links
Social links
https://www.facebook.com/ThePebbleHollowGarden
https://www.instagram.com/thepebblehollowgardennursery

Two local native nursery websites that I like the style of:
https://www.brimbarkstemnursery.com.au/
https://www.telvoni.com.au/

I'm using two versions of our logo, we have the smaller circle and then the other logo which is stretched out. We have used the second design for our signs at the nursery, I've asked the sign guy for a copy of the design as I don't currently have one. I have vector files of the other design.

We have wordpress set up with elemantor and hosting with godaddy, I can send you the logon details once design is confirmed.

Target Market(s)

Anyone who likes gardening, we have a pretty even spread of customers across male/female and all ages

Industry/Entity Type

Garden centre with native plants, flowers and giftwear

Coding

Coded - Design and coding required

Colors
0054AA
0677BA
7BADD7
CADEEF
E8F1F8
0094D4
00A9DD
6FCCEA
C7EBF8
E9F6FB
00AB8E
00BBA5
67D7C9
C6EFE9
E9F9F6

Requirements
Must have
• Organic/modern/minimalist design
Nice to have
• Blue/white/green, flannel flowers as per logo

```html
<!DOCTYPE html>
<html lang="en">
<head>
<meta charset="utf-8">
<title>The Pebble Hollow Garden — Native Nursery</title>
<link href="https://fonts.googleapis.com/css2?family=Montserrat:wght@400;800&family=Poppins:wght@500;600&family=Roboto:wght@400;500;700&family=Nunito+Sans:wght@400&display=swap" rel="stylesheet">
<style>
:root{
  --blue:#0054AA;
  --teal:#00AB8E;
  --teal-light:#00BBA5;
  --ink:#222222;
  --text:#333333;
  --white:#ffffff;
  --black:#000000;
}
*{box-sizing:border-box;margin:0;padding:0}
html,body{width:1200px;height:3285px;overflow:hidden;background:var(--white)}
body{position:relative;font-family:"Roboto",sans-serif;color:var(--text)}
a{color:inherit;text-decoration:none}

/* header */
.site-header{position:absolute;left:0;top:0;width:1200px;height:105px;background:var(--white);z-index:5}
.brand-badge{position:absolute;left:94px;top:-8px;width:170px;height:170px;border-radius:50%;background:var(--white);z-index:6;display:flex;align-items:center;justify-content:center}
.brand-badge .ring{position:absolute;left:20px;top:20px;width:130px;height:130px;border-radius:50%;border:1.5px solid #444}
.brand-name{font-family:"Roboto",sans-serif;font-weight:400;font-size:15px;line-height:1.25;color:#333;text-align:center;position:relative;margin-top:20px}
.main-nav{position:absolute;top:50px;left:0;font-family:"Roboto",sans-serif;font-size:16px;color:#111;letter-spacing:.2px}
.main-nav a{position:absolute;white-space:nowrap}
.header-icon{position:absolute;top:50px;width:18px;height:18px}
.btn{position:absolute;display:flex;align-items:center;justify-content:center;background:var(--blue);color:var(--white);font-family:"Roboto",sans-serif;font-weight:700;font-size:15px;border-radius:8px;border-right:3px solid var(--teal);border-bottom:3px solid var(--teal);letter-spacing:.2px}

/* hero */
.hero{position:absolute;left:0;top:105px;width:1200px;height:700px;background:linear-gradient(100deg,#1f3a24 0%,#3f5a34 30%,#7a4050 58%,#c9546f 72%,#e07a92 82%,#5b4a38 100%)}
.hero-kicker{position:absolute;left:111px;top:232px;font-family:"Montserrat",sans-serif;font-weight:400;font-size:52px;color:var(--white);letter-spacing:.5px}
.hero-title{position:absolute;left:111px;top:305px;font-family:"Montserrat",sans-serif;font-weight:800;font-size:68px;line-height:78px;color:var(--white);white-space:nowrap}
.hero-lede{position:absolute;left:111px;top:474px;width:410px;font-size:16px;line-height:23px;color:var(--white)}
.hero-dots{position:absolute;left:582px;top:642px;display:flex;gap:5px;align-items:center}
.hero-dots span{width:9px;height:9px;border-radius:50%;background:var(--white)}
.hero-dots .on{width:13px;height:13px;border:3px solid var(--white);background:var(--blue)}
.wave{position:absolute;left:0;width:1200px}

/* features */
.feature-title{position:absolute;font-family:"Poppins",sans-serif;font-weight:500;font-size:27px;color:var(--ink);letter-spacing:.3px}
.feature-copy{position:absolute;font-size:15.5px;line-height:25.7px;color:#333}
.feature-copy span{display:block}
.centered{text-align:center}
.photo{position:absolute}
.nursery-photo{left:99px;top:848px;width:434px;height:434px;border-radius:50%;border:5px solid #555;background:radial-gradient(circle at 45% 30%,#6d9fd6 0%,#5d8a55 38%,#3e5f34 62%,#8a8378 100%)}

/* footer */
.site-footer{position:absolute;left:0;top:2955px;width:1200px;height:330px;background:var(--black);color:var(--white)}
.footer-badge{position:absolute;left:170px;top:2962px;width:196px;height:196px;border-radius:50%;border:2px solid var(--white);display:flex;align-items:center;justify-content:center;text-align:center;font-size:21px;line-height:1.25;color:var(--white)}
.footer-heading{position:absolute;top:2990px;font-family:"Roboto",sans-serif;font-weight:700;font-size:19px;color:var(--white)}
.footer-links{position:absolute;top:3034px;list-style:none;font-size:15.5px;line-height:25.6px;color:var(--white)}
.contact-line{position:absolute;left:838px;font-family:"Nunito Sans",sans-serif;font-size:15.5px;line-height:25.6px;color:var(--white)}
.contact-icon{position:absolute;left:811px;width:15px;height:15px}
.copyright{position:absolute;left:111px;top:3208px;font-family:"Nunito Sans",sans-serif;font-size:15px;color:var(--white)}
.social{position:absolute;top:3196px;width:32px;height:32px;border-radius:50%;border:1.5px solid var(--white)}
</style>
</head>
<body>

<header class="site-header">
  <nav class="main-nav">
    <a style="left:335px" href="#nursery">NURSERY</a>
    <a style="left:450px" href="#native-flowers">NATIVE FLOWERS</a>
    <a style="left:625px" href="#giftwear">GIFTWEAR</a>
    <a style="left:748px" href="#about">ABOUT US</a>
  </nav>
  <svg class="header-icon" style="left:895px" viewBox="0 0 20 20" aria-label="Search"><circle cx="8" cy="8" r="6" fill="none" stroke="#33435a" stroke-width="3"/><line x1="12.5" y1="12.5" x2="18" y2="18" stroke="#33435a" stroke-width="3.2" stroke-linecap="round"/></svg>
  <svg class="header-icon" style="left:933px" viewBox="0 0 20 20" aria-label="Account"><circle cx="10" cy="6" r="4.5" fill="#33435a"/><path d="M2 19c0-5 3.5-7.5 8-7.5s8 2.5 8 7.5z" fill="#33435a"/></svg>
  <a class="btn" style="left:982px;top:38px;width:104px;height:42px" href="#login">LOG IN</a>
</header>
<div class="brand-badge"><span class="ring"></span><span class="brand-name">The Pebble<br>Hollow Garden</span></div>

<section class="hero" role="img" aria-label="Close-up photograph of pink kangaroo paw flowers in bloom"></section>
<p class="hero-kicker">WELCOME TO</p>
<h1 class="hero-title">PEBBLE HOLLOW<br>GARDEN</h1>
<p class="hero-lede">At our nursery, we provide native plants that thrive in their local environment.</p>
<a class="btn" style="left:111px;top:544px;width:129px;height:44px" href="#shop">SHOP NOW</a>
<div class="hero-dots"><span></span><span class="on"></span><span></span></div>
<svg class="wave" style="top:640px;height:166px" viewBox="0 0 1200 166" preserveAspectRatio="none" aria-hidden="true">
  <path d="M0 87 C120 30 280 0 420 4 C700 12 950 110 1200 150 L1200 166 L0 166Z" fill="#00AB8E"/>
  <path d="M0 166 L0 150 C130 80 300 38 460 38 C700 40 950 130 1200 160 L1200 166Z" fill="#ffffff"/>
</svg>

<!-- Nursery -->
<div class="photo nursery-photo" role="img" aria-label="Photograph of the nursery garden path lined with potted native plants, framed in a circle"></div>
<h2 class="feature-title" id="nursery" style="left:671px;top:867px">NURSERY</h2>
<p class="feature-copy" style="left:671px;top:933px;width:418px;text-align:justify">
  <span>Welcome to our native plant nursery information page!</span>
  <span>At our nursery, we provide native plants that thrive in their local environment. Native plants are essential for preserving biodiversity, and they support pollinators and other wildlife while reducing human impact on the environment.</span>
  <span>At our nursery, we offer a wide selection of native plants that are suitable for a variety of different environments, and we provide planting and care instructions to ensure that your plants thrive once they’re in the ground.</span>
</p>
<a class="btn" style="left:669px;top:1192px;width:131px;height:43px" href="#nursery">LEARN MORE</a>

<!-- Native flowers -->
<div class="photo" style="left:514px;top:1374px;width:686px;height:471px;background:linear-gradient(135deg,#8a2e3a 0%,#e6d3c8 35%,#f0c53a 55%,#f4f1ea 75%,#d9b84a 100%)" role="img" aria-label="Photograph of a bright bouquet of Australian native flowers"></div>
<h2 class="feature-title centered" id="native-flowers" style="left:100px;top:1454px;width:376px">NATIVE FLOWERS</h2>
<p class="feature-copy centered" style="left:110px;top:1518px;width:356px">At the nursery, we specialize in creating unique arrangements using locally sourced native Australian flowers. Our team of experienced florists are passionate about showcasing the beauty of our country’s flora and fauna through unique and beautiful bespoke floral designs.</p>
<a class="btn" style="left:223px;top:1711px;width:131px;height:43px" href="#native-flowers">LEARN MORE</a>

<!-- Giftwear -->
<div class="photo" style="left:0;top:1845px;width:686px;height:472px;background:linear-gradient(120deg,#3b4a34 0%,#4d6a3a 30%,#9c98d8 50%,#5a7040 68%,#1f2420 100%)" role="img" aria-label="Photograph of lilac fan flowers growing in a nursery pot"></div>
<h2 class="feature-title centered" id="giftwear" style="left:724px;top:1944px;width:376px">GIFTWEAR</h2>
<p class="feature-copy centered" style="left:730px;top:2007px;width:364px">We are proud to offer a wide range of unique and high-quality gifts that celebrate the natural beauty of Australia’s native flora and fauna. From beautifully scented candles to stunning artworks, our gift selection is sure to please.</p>
<a class="btn" style="left:847px;top:2167px;width:131px;height:43px" href="#giftwear">LEARN MORE</a>

<!-- About -->
<div class="photo" style="left:514px;top:2317px;width:686px;height:560px;background:linear-gradient(160deg,#3f6a33 0%,#5d8a45 40%,#c86a86 65%,#4b6b35 100%)" role="img" aria-label="Photograph of pink kangaroo paw plants in the nursery garden"></div>
<h2 class="feature-title centered" id="about" style="left:100px;top:2418px;width:376px">ABOUT US</h2>
<p class="feature-copy centered" style="left:108px;top:2481px;width:360px">The Pebble Hollow Garden business, that has been providing plants, flowers and native giftware to the Central Coast and surrounding areas since 2001. Over this time, we have established a strong connection with the community and provided expert native advice.</p>
<a class="btn" style="left:223px;top:2662px;width:131px;height:43px" href="#about">LEARN MORE</a>

<svg class="wave" style="top:2700px;height:262px" viewBox="0 0 1200 262" preserveAspectRatio="none" aria-hidden="true">
  <path d="M0 51 C150 150 300 170 514 160 C800 140 1000 100 1200 70 L1200 262 L0 262Z" fill="#00AB8E"/>
  <path d="M0 143 C150 190 300 200 480 197 C800 190 1000 140 1200 105 L1200 262 L0 262Z" fill="#000000"/>
</svg>

<footer class="site-footer"></footer>
<div class="footer-badge">The Pebble<br>Hollow Garden</div>

<h3 class="footer-heading" style="left:458px">QUICK LINKS</h3>
<ul class="footer-links" style="left:458px">
  <li><a href="#nursery">Nursery</a></li>
  <li><a href="#native-flowers">Native flowers</a></li>
  <li><a href="#giftwear">Giftwear</a></li>
  <li><a href="#about">About us</a></li>
</ul>
<h3 class="footer-heading" style="left:643px">COMPANY</h3>
<ul class="footer-links" style="left:643px">
  <li><a href="#terms">Terms &amp; Conditions</a></li>
  <li><a href="#privacy">Privacy Policy</a></li>
  <li><a href="#about">About Us</a></li>
  <li><a href="#support">Support</a></li>
</ul>
<h3 class="footer-heading" style="left:811px">CONTACT US</h3>
<svg class="contact-icon" style="top:3041px" viewBox="0 0 16 16" aria-hidden="true"><path d="M8 1a5 5 0 0 0-5 5c0 4 5 9 5 9s5-5 5-9a5 5 0 0 0-5-5z" fill="#fff"/><circle cx="8" cy="6" r="2" fill="#000"/></svg>
<p class="contact-line" style="top:3034px">27 Saltbush Road,<br>Kelvindale, NSW, Australia, 2261</p>
<svg class="contact-icon" style="top:3098px" viewBox="0 0 16 16" aria-hidden="true"><path d="M3 1l3 0 1.5 4-2 1.3a9 9 0 0 0 4.2 4.2L11 8.5l4 1.5v3a2 2 0 0 1-2 2C7 15 1 9 1 3a2 2 0 0 1 2-2z" fill="#fff"/></svg>
<p class="contact-line" style="top:3093px">+61 2 4718 2093</p>
<svg class="contact-icon" style="top:3135px" viewBox="0 0 16 16" aria-hidden="true"><rect x="1" y="3" width="14" height="10" rx="1" fill="#fff"/><path d="M1.5 4l6.5 5 6.5-5" fill="none" stroke="#000" stroke-width="1.4"/></svg>
<p class="contact-line" style="top:3128px">hello@pebblehollowgarden.com.au</p>

<p class="copyright">©Copyrights 2023 Pebble Hollow Garden &nbsp; | &nbsp; All Rights Reserved</p>
<a class="social" style="left:1010px" href="#social-one" aria-label="Social profile one"></a>
<a class="social" style="left:1052px" href="#social-two" aria-label="Social profile two"></a>

</body>
</html>
```